Business Card Design

Online clothing womens clothing store, I sell my clothing online and at the markets.

i would like the attached picture on the front of the card and the contact information on the back.

Industry/Entity Type

Business

Contact Information for Business Card

Marlow Thread
Karen Whitfield
(Instagram symbol) _marlow_thread_
(Facebook symbol) www.fakebookexample.com/marlowthreadau/

W : www.marlowthread.example.au
E : info@marlowthread.example.au
P : 0498716204

```html
<!DOCTYPE html>
<html lang="en">
<head>
<meta charset="utf-8">
<title>Marlow Thread – Business Card</title>
<link href="https://fonts.googleapis.com/css2?family=Open+Sans:wdth,wght@75..100,400;75..100,700&display=swap" rel="stylesheet">
<style>
  :root {
    --stage-bg: #121212;
    --card-back: #f3f3f3;
    --ink: #111111;
    --front-light: #e4eaea;
    --front-mist: #a9bcbc;
    --front-teal: #7f9697;
    --front-deep: #5d6c70;
    --front-type: #f6f6f4;
  }
  * { box-sizing: border-box; margin: 0; padding: 0; }
  html, body {
    width: 1200px;
    height: 900px;
    overflow: hidden;
    background: var(--stage-bg);
    font-family: "Open Sans", sans-serif;
  }
  .stage {
    position: relative;
    width: 1200px;
    height: 900px;
  }
  .card {
    position: absolute;
    top: 184px;
    height: 491px;
    border-radius: 12px;
    overflow: hidden;
  }
  .card--contact {
    left: 299px;
    width: 301px;
    background: var(--card-back);
    color: var(--ink);
    text-align: center;
  }
  .card__name {
    position: absolute;
    top: 100px;
    width: 100%;
    font-size: 15.5px;
    font-weight: 700;
    letter-spacing: 0.3px;
    white-space: nowrap;
  }
  .contact-list {
    position: absolute;
    top: 200px;
    width: 100%;
    list-style: none;
    font-size: 12.5px;
    line-height: 20px;
  }
  .social-list {
    position: absolute;
    top: 343px;
    width: 100%;
    list-style: none;
    font-size: 12.5px;
    line-height: 20px;
  }
  .contact-line {
    display: flex;
    justify-content: center;
    align-items: center;
    gap: 7px;
    white-space: nowrap;
  }
  .contact-line svg { flex: none; }
  .social-mark {
    display: inline-block;
    width: 7px;
    height: 7px;
    background: var(--ink);
    flex: none;
  }
  .card--brand {
    left: 645px;
    width: 305px;
  }
  .brand-photo {
    position: absolute;
    inset: 0;
    background:
      radial-gradient(ellipse 45% 40% at 35% 48%, var(--front-light) 0%, rgba(228,234,234,0) 100%),
      radial-gradient(ellipse 50% 45% at 55% 58%, var(--front-deep) 0%, rgba(93,108,112,0) 100%),
      linear-gradient(160deg, var(--front-mist) 0%, var(--front-teal) 55%, var(--front-deep) 100%);
  }
  .brand-name {
    position: absolute;
    top: 404px;
    width: 100%;
    text-align: center;
    font-size: 32px;
    line-height: 1;
    font-weight: 700;
    font-stretch: 75%;
    font-variation-settings: "wdth" 75;
    letter-spacing: 0.5px;
    white-space: nowrap;
    color: var(--front-type);
  }
</style>
</head>
<body>
<main class="stage">
  <section class="card card--contact">
    <h1 class="card__name">KAREN WHITFIELD</h1>
    <ul class="contact-list">
      <li class="contact-line">
        <svg width="11" height="11" viewBox="0 0 24 24" aria-hidden="true"><path fill="#111" d="M6.6 10.8a15.1 15.1 0 0 0 6.6 6.6l2.2-2.2a1 1 0 0 1 1-.25 11.4 11.4 0 0 0 3.6.57 1 1 0 0 1 1 1V20a1 1 0 0 1-1 1A17 17 0 0 1 3 4a1 1 0 0 1 1-1h3.5a1 1 0 0 1 1 1c0 1.250.2 2.45.57 3.57a1 1 0 0 1-.25 1z"/></svg>
        <span>0498716204</span>
      </li>
      <li class="contact-line">
        <svg width="12" height="9" viewBox="0 0 24 18" aria-hidden="true"><rect width="24" height="18" fill="#111"/><path d="M1 1l11 9 11-9" fill="none" stroke="#f3f3f3" stroke-width="2"/></svg>
        <span>info@marlowthread.example.au</span>
      </li>
      <li class="contact-line">
        <svg width="12" height="12" viewBox="0 0 24 24" aria-hidden="true"><g fill="none" stroke="#111" stroke-width="2.6" stroke-linecap="round"><path d="M10 14a5 5 0 0 0 7 0l3-3a5 5 0 0 0-7-7l-1.5 1.5"/><path d="M14 10a5 5 0 0 0-7 0l-3 3a5 5 0 0 0 7 7l1.5-1.5"/></g></svg>
        <span>www.marlowthread.example.au</span>
      </li>
    </ul>
    <ul class="social-list">
      <li class="contact-line"><span class="social-mark"></span><span>_marlow_thread_</span></li>
      <li class="contact-line"><span class="social-mark"></span><span>/marlowthreadau/</span></li>
    </ul>
  </section>

  <section class="card card--brand">
    <div class="brand-photo" role="img" aria-label="Soft misty photograph in pale teal and smoky grey tones"></div>
    <p class="brand-name">MARLOW THREAD</p>
  </section>
</main>
</body>
</html>
```